Business Card design for insurance broker in Denver, CO, USA

I need a business card designed using this logo that was just created. We sell life and disability income insurance to US consumers.
Looking for a professionally designed card to make use of the logo and have something to hand to prospects or new business referral sources. The card could be white, gray, black or whatever you would recommend.

Target Market(s)

US Consumers and other financial professionals that I partner with.

Industry/Entity Type

Insurance Broker

Contact Information for Business Card

Owen T. Farrow, CLU, LUTCF (please note that CLU should have a superscript R in a circle for registered trademark)
President
phone (303) 555-0187
email owen@keelbrookcover.example
4620 W. Halvern Rd, Suite 300, Greenwood Village, CO 80111
Somewhere fit in a tagline saying "Your resource for life, long term care, and disability insurance" (maybe the back if it doesn't fit on the front, your call)

Font styles to use
Sans Serif

Requirements
Must have
• Must have logo in correct blue and gray colors, my name, address, phone, email. Order and placement determined by the designer.
• I just want something that looks a more professional than what I could have done using the business card designer tool on pixelbazaar.example or QuillPress, or any other do-it-yourself tool
• A regular rectangular business card with square corners is preferred
Nice to have
• I included the logos of 2 organizations I belong to (GKLS and WOBCE). They should be small, but visible on the back only. If it doesn’t look good, this is not a requirement, feel free to drop it.
Should not have
• Do not add any colors not already in the logo, except use of black and whites which are okay. If you use the logo on the back and want to make that in all black, gray or white, that may be okay as well.

```html
<!DOCTYPE html>
<html lang="en">
<head>
<meta charset="utf-8">
<title>Keelbrook Insurance Solutions – Business Card</title>
<link rel="stylesheet" href="https://fonts.googleapis.com/css2?family=Open+Sans:wght@400;600;700&display=swap">
<style>
  :root {
    --brand-blue: #1b87d2;
    --brand-blue-dark: #1470b8;
    --brand-gray: #8a8c8e;
    --ink: #2e2f31;
    --paper: #ffffff;
    --paper-shade: #f1f1f1;
    --backdrop: #2b2b2d;
  }
  * { box-sizing: border-box; margin: 0; padding: 0; }
  html, body { width: 1200px; height: 1000px; overflow: hidden; }
  body {
    background: var(--backdrop);
    font-family: "Open Sans", Arial, sans-serif;
    position: relative;
  }
  .card {
    position: absolute;
    left: 250px;
    width: 700px;
    height: 400px;
    overflow: hidden;
  }

  /* ---------- Back ---------- */
  .card-back {
    top: 60px;
    background: linear-gradient(160deg, #2a97de 0%, var(--brand-blue) 55%, var(--brand-blue-dark) 100%);
    color: var(--paper);
  }
  .back-badges {
    position: absolute;
    top: 26px;
    right: 30px;
    display: flex;
    gap: 16px;
  }
  .badge {
    width: 38px;
    height: 38px;
    border-radius: 50%;
    background: rgba(255,255,255,0.55);
  }
  .badge.square { border-radius: 4px; width: 44px; height: 30px; margin-top: 4px; }
  .back-name {
    position: absolute;
    top: 140px;
    left: 0;
    right: 0;
    text-align: center;
    font-size: 52px;
    font-weight: 700;
    letter-spacing: 2px;
  }
  .back-tagline {
    position: absolute;
    top: 250px;
    left: 0;
    right: 0;
    text-align: center;
    font-size: 17px;
    font-weight: 400;
  }

  /* ---------- Front ---------- */
  .card-front {
    top: 540px;
    background: linear-gradient(135deg, var(--paper) 0%, var(--paper) 60%, var(--paper-shade) 100%);
  }
  .front-name {
    position: absolute;
    left: 34px;
    top: 118px;
    color: var(--brand-blue);
    font-size: 27px;
    font-weight: 700;
    line-height: 1.02;
    text-transform: uppercase;
  }
  .front-divider {
    position: absolute;
    left: 330px;
    top: 105px;
    width: 1px;
    height: 180px;
    background: linear-gradient(to bottom, rgba(138,140,142,0), var(--brand-gray) 25%, var(--brand-gray) 75%, rgba(138,140,142,0));
  }
  .contact {
    position: absolute;
    left: 352px;
    top: 102px;
    color: var(--ink);
    font-size: 16px;
    line-height: 1.35;
  }
  .contact .person {
    color: var(--brand-blue);
    font-weight: 700;
    font-size: 17px;
    letter-spacing: 0.5px;
    text-transform: uppercase;
  }
  .contact .person sup { font-size: 9px; }
  .contact .role {
    color: var(--brand-gray);
    font-size: 15px;
    text-transform: uppercase;
    margin-bottom: 8px;
  }
  .contact .line { display: flex; align-items: center; gap: 8px; }
  .contact .line svg { width: 14px; height: 14px; flex: none; fill: var(--brand-blue); }
  .front-band {
    position: absolute;
    left: 0;
    top: 296px;
    width: 700px;
    height: 34px;
    display: flex;
  }
  .front-band .url {
    flex: 1;
    background: var(--brand-blue);
    color: var(--paper);
    font-size: 19px;
    letter-spacing: 1.5px;
    padding-left: 120px;
    line-height: 34px;
  }
  .front-band .end {
    width: 110px;
    background: linear-gradient(to right, #9a9c9e, #c4c5c6);
  }
</style>
</head>
<body>

  <section class="card card-back" aria-label="Business card back">
    <div class="back-badges">
      <div class="badge square" role="img" aria-label="Member organisation badge"></div>
      <div class="badge" role="img" aria-label="Member organisation badge"></div>
    </div>
    <p class="back-name">KEELBROOK</p>
    <p class="back-tagline">Your resource for life, long term care, &amp; disability insurance</p>
  </section>

  <section class="card card-front" aria-label="Business card front">
    <p class="front-name">Keelbrook<br>Insurance<br>Solutions</p>

    <div class="front-divider"></div>

    <div class="contact">
      <p class="person">Owen T. Farrow, CLU<sup>®</sup>, LUTCF</p>
      <p class="role">CEO/Founder</p>
      <p>4620 W. Halvern Rd, Suite 300</p>
      <p>Ashcombe Village, CO 80190</p>
      <p class="line">
        <svg viewBox="0 0 16 16" aria-hidden="true"><path d="M3.5 1.5l2.5 0 1 3.5-1.8 1.2a9 9 0 0 0 4.6 4.6L11 9l3.5 1v2.5c0 1-1 2-2 2A11 11 0 0 1 1.5 3.5c0-1 1-2 2-2z"/></svg>
        (303) 555-0187
      </p>
      <p class="line">
        <svg viewBox="0 0 16 16" aria-hidden="true"><path d="M1 3h14v10H1z M1.5 3.5L8 9l6.5-5.5" stroke="#fff" stroke-width="1"/></svg>
        owen@keelbrookcover.example
      </p>
    </div>

    <div class="front-band">
      <div class="url">www.keelbrookcover.example</div>
      <div class="end"></div>
    </div>
  </section>

</body>
</html>
```